Website redesign for Halt and Fullmane

We would like to update the design of our current website to a more concise, conversion optimized design.
The goal of our website is to get our message across as concisely as possible plus encourage people to contact us for more information or to book a consultation.
We need a redesign of the home page and 1 internal page - just for design/layout purposes/format purposes.

Target Market(s)

Males 20-45 years old who are concerned about hair loss and who want to regrow their own hair.

Industry/Entity Type

Health And Wellness

Number of Pages Required

2 page

Font styles to use
Sans Serif

Colors
00a990
33a6d7
ffffff
9d9d9d

Requirements
Must have
• We want the home page to be very concise and to the point in getting the message across. We want to get across the following 6 key messages:
• 1. Dr Pembrook story – why he created this solution
• 2. Hair loss is caused by a chemical imbalance
• 3. Halt and fullmane conducts genetic and DNA analysis, then rebalances body chemistry, thus reversing the hair loss process and enabling your own hair to regrow naturally
• 4. Money back guaranteed results
• 5. Purely Core ingredients – no harsh preservatives or chemicals are included
• 6. All ingredients are FDA approved and safe – no side effects
• We also need a strong call to action. We want people to call or email us to find out more information or to schedule a consultation.
• Here is our current website which is not performing as we would hope: http://www.haltandfullmane.example/
• Here is our press release for further information: https://www.pressdeskhub.example/news/finally-we-now-have-a-cure-for-male-pattern-baldness-28461902
• I uploaded the logo files, but let me know if anything else is needed and I can add it.

```html
<!DOCTYPE html>
<html lang="en">
<head>
<meta charset="utf-8">
<title>Halt &amp; Fullmane — Home</title>
<link href="https://fonts.googleapis.com/css2?family=Lato:wght@400;700;900&family=Open+Sans:wght@400;600;700&family=Noto+Serif:wght@400;700&display=swap" rel="stylesheet">
<style>
:root{
  --green-deep:#0a5f4c;
  --green-footer:#08503f;
  --teal:#00a990;
  --blue:#33a6d7;
  --white:#ffffff;
  --grey:#9d9d9d;
  --ink:#222222;
  --body:#666666;
  --line:#e2e2e2;
}
*{box-sizing:border-box;margin:0;padding:0}
html,body{width:1200px;height:3396px;overflow:hidden}
body{font-family:"Open Sans",Arial,sans-serif;color:var(--ink);background:var(--white);position:relative}
.abs{position:absolute}

/* header */
.site-header{position:absolute;left:0;top:0;width:1200px;height:109px;background:var(--white)}
.brand{position:absolute;left:100px;top:28px;display:flex;align-items:center;gap:14px}
.brand-mark{width:34px;height:34px;border-radius:50%;background:var(--teal)}
.brand-name{font-family:"Lato",sans-serif;font-size:30px;color:var(--green-deep);line-height:1}
.brand-sub{font-family:"Lato",sans-serif;font-size:15px;color:var(--blue);margin-top:4px}
.header-call{position:absolute;left:782px;top:36px;display:flex;align-items:center;gap:10px}
.header-call .label{font-size:10px;color:var(--ink);font-weight:600}
.header-call .num{font-size:18px;font-weight:700;color:var(--ink)}
.header-cta{position:absolute;left:952px;top:32px;width:148px;height:46px;background:#eeeeee;border:1px solid #dcdcdc;border-radius:3px;text-align:center;font-size:12px;color:#555;padding-top:6px;line-height:1.3}
.header-cta b{color:var(--blue);font-weight:700}

/* hero */
.hero{position:absolute;left:0;top:109px;width:1200px;height:484px;overflow:hidden}
.hero-photo{position:absolute;inset:0;background:linear-gradient(90deg,#d9d6d2 0%,#c7c4c0 35%,#f2f2f2 60%,#e6e8ea 100%)}
.main-nav{position:absolute;left:0;top:0;width:1200px;height:54px;background:rgba(70,70,70,.55);display:flex;align-items:center;padding-left:100px;gap:0}
.main-nav a{color:var(--white);text-decoration:none;font-family:"Lato",sans-serif;font-weight:700;font-size:14px;margin-right:47px;letter-spacing:.2px}
.hero-title{position:absolute;left:0;top:195px;width:1200px;text-align:center;font-family:"Lato",sans-serif;font-weight:700;color:var(--white);font-size:38px;line-height:50px;text-shadow:0 2px 6px rgba(0,0,0,.35)}
.dots{position:absolute;display:flex;gap:12px}
.dot{width:14px;height:14px;border-radius:50%;background:var(--white)}
.dot.on{background:var(--blue)}

/* story */
.story-title{position:absolute;left:100px;top:706px;font-family:"Lato",sans-serif;font-weight:700;font-size:26px}
.story-lead{position:absolute;left:100px;top:762px;width:480px;font-size:13px;font-weight:700;line-height:24px;text-transform:uppercase}
.story-text{position:absolute;left:100px;top:818px;width:480px;font-size:12px;color:var(--body);line-height:23px}
.btn-outline{position:absolute;left:100px;top:916px;width:120px;height:44px;border:2px solid var(--green-deep);border-radius:4px;font-size:12px;font-weight:600;text-align:center;line-height:40px;color:var(--ink)}
.story-photo{position:absolute;left:641px;top:686px;width:459px;height:299px;border:5px solid #f1f1f1;box-shadow:0 0 4px rgba(0,0,0,.15);background:linear-gradient(135deg,#e3e3e0 0%,#bfc9c4 45%,#8c9e98 70%,#e8e8e6 100%)}

/* benefits */
.benefits-photo{position:absolute;left:0;top:1082px;width:600px;height:424px;background:linear-gradient(90deg,#6f6a66 0%,#c9c5c1 30%,#e9e6e2 60%,#b9b4b0 100%)}
.benefits{position:absolute;left:600px;top:1082px;width:600px;height:424px;background:var(--green-deep);color:var(--white);padding:60px 52px}
.benefits h2{font-family:"Lato",sans-serif;font-weight:700;font-size:26px;margin-bottom:26px}
.benefits li{list-style:none;display:flex;gap:14px;font-size:13px;line-height:19px;margin-bottom:14px}
.benefits li svg{flex:none;margin-top:3px}

/* blog */
.section-title{position:absolute;left:0;width:1200px;text-align:center;font-family:"Noto Serif",serif;font-weight:700;font-size:24px}
.section-sub{position:absolute;left:0;width:1200px;text-align:center;font-family:"Noto Serif",serif;font-size:12px;color:var(--body)}
.post{position:absolute;top:1693px;width:305px}
.post-photo{height:209px;border-radius:4px;position:relative}
.post-date{position:absolute;left:0;top:0;width:220px;height:40px;background:var(--blue);color:var(--white);font-size:15px;font-weight:600;display:flex;align-items:center;padding-left:22px;gap:10px;border-radius:4px 0 0 0}
.post-meta{margin-top:36px;font-size:11px;color:var(--body);display:flex;gap:26px}
.post h3{font-family:"Lato",sans-serif;font-weight:700;font-size:16px;margin-top:18px}
.post p{font-size:12px;color:var(--body);line-height:19px;margin-top:12px}

/* testimonial */
.testimonial{position:absolute;left:0;top:2135px;width:1200px;height:426px;background:linear-gradient(90deg,#5b4e46 0%,#8c7f77 35%,#b8aca4 65%,#6e625b 100%)}
.quote-rule{position:absolute;top:111px;width:184px;height:2px;background:var(--white)}
.quote-badge{position:absolute;left:553px;top:78px;width:86px;height:86px;border:3px solid var(--white);border-radius:50%}
.quote-text{position:absolute;left:0;top:186px;width:1200px;text-align:center;color:var(--white);font-size:17px;line-height:30px;font-weight:600}
.quote-name{position:absolute;left:0;top:262px;width:1200px;text-align:center;color:var(--white);font-size:12px;font-weight:700}

/* partners */
.partner{position:absolute;top:2746px;width:186px;height:107px;border:1px solid var(--line);background:var(--white);display:flex;align-items:center;justify-content:center}
.partner span{display:block;width:96px;height:44px;border-radius:4px;background:#d6d6d6}

/* contact */
.contact{position:absolute;left:0;top:2943px;width:1200px;height:313px;background:var(--green-deep);color:var(--white)}
.contact-item{position:absolute;top:86px;width:300px;text-align:center;font-size:16px;font-weight:700;line-height:24px}
.contact-icon{width:70px;height:70px;border:2px solid var(--white);border-radius:50%;margin:0 auto 28px;display:flex;align-items:center;justify-content:center}

/* footer */
.site-footer{position:absolute;left:0;top:3256px;width:1200px;height:140px;background:var(--green-footer);color:var(--white)}
.copyright{position:absolute;left:100px;top:61px;font-size:12px}
.social{position:absolute;left:757px;top:46px;display:flex;gap:17px}
.social span{width:46px;height:46px;border:2px solid var(--white);border-radius:50%;display:block}
</style>
</head>
<body>

<header class="site-header">
  <div class="brand">
    <span class="brand-mark"></span>
    <div><div class="brand-name">Halt &amp; Fullmane</div><div class="brand-sub">by Gavin Pembrook M.D.</div></div>
  </div>
  <div class="header-call">
    <svg width="38" height="38" viewBox="0 0 38 38"><circle cx="19" cy="19" r="17" fill="none" stroke="#0a5f4c" stroke-width="3"/><path d="M13 11c1.5-1 2.5 0 3.5 2l1 2c.5 1-.5 2-1.5 2.5 1 2.5 3 4.5 5.5 5.5.5-1 1.5-2 2.5-1.5l2 1c2 1 3 2 2 3.5-1.5 2-4 2.5-7 1-4-2-7-5-8.5-9-1-3-.5-5.5.5-7z" fill="#0a5f4c"/></svg>
    <div><div class="label">Call to Action</div><div class="num">(555) 014-2290</div></div>
  </div>
  <div class="header-cta">Questions?<br><b>CALL NOW!</b></div>
</header>

<section class="hero">
  <div class="hero-photo" role="img" aria-label="Photo of a doctor in gloves examining a patient's scalp"></div>
  <nav class="main-nav">
    <a>ABOUT US</a><a>HOW IT WORKS</a><a>SUCCESS STORIES</a><a>FAQS</a><a>BLOG</a><a>SALON</a><a>PARTNERS</a><a>BOOK NOW</a><a>CONTACT</a>
  </nav>
  <h1 class="hero-title">STOP &nbsp;HAIR LOSS AND REGROW A FULL,<br>HEALTHY HEAD OF HAIR</h1>
  <div class="dots" style="left:537px;top:411px"><span class="dot"></span><span class="dot"></span><span class="dot on"></span><span class="dot"></span><span class="dot"></span></div>
</section>

<section>
  <h2 class="story-title">DR. PEMBROOK’S STORY</h2>
  <p class="story-lead">Discovery and development of the Halt &amp; Fullmane™ hair loss solution.</p>
  <p class="story-text">Dr. Gavin Pembrook is a renowned hair restoration expert and was even a contributor in the development of the Advanced High Density MICROscopic single hair transplant procedure. As a practicing derma-surgeon.</p>
  <div class="btn-outline">READ MORE</div>
  <div class="story-photo" role="img" aria-label="Photo of the doctor treating a client's hair in a clinic"></div>
</section>

<div class="benefits-photo" role="img" aria-label="Photo of shelves lined with hair care bottles"></div>
<section class="benefits">
  <h2>OUR &nbsp;BENEFITS</h2>
  <ul>
    <li><svg width="14" height="14" viewBox="0 0 14 14"><path d="M1 7l4 4 8-9" fill="none" stroke="#fff" stroke-width="2"/></svg>Dr Pembrook story – why he created this solution</li>
    <li><svg width="14" height="14" viewBox="0 0 14 14"><path d="M1 7l4 4 8-9" fill="none" stroke="#fff" stroke-width="2"/></svg>Hair loss is caused by a chemical imbalance</li>
    <li><svg width="14" height="14" viewBox="0 0 14 14"><path d="M1 7l4 4 8-9" fill="none" stroke="#fff" stroke-width="2"/></svg>Halt and fullmane conducts genetic and DNA analysis, then rebalances body chemistry, thus reversing the hair loss process and enabling your own hair to regrow naturally</li>
    <li><svg width="14" height="14" viewBox="0 0 14 14"><path d="M1 7l4 4 8-9" fill="none" stroke="#fff" stroke-width="2"/></svg>Money back guaranteed results</li>
    <li><svg width="14" height="14" viewBox="0 0 14 14"><path d="M1 7l4 4 8-9" fill="none" stroke="#fff" stroke-width="2"/></svg>Purely Core ingredients – no harsh preservatives or chemicals are included</li>
    <li><svg width="14" height="14" viewBox="0 0 14 14"><path d="M1 7l4 4 8-9" fill="none" stroke="#fff" stroke-width="2"/></svg>All ingredients are FDA approved and safe – no side effects</li>
  </ul>
</section>

<section>
  <h2 class="section-title" style="top:1598px">LATEST BLOG POST</h2>
  <p class="section-sub" style="top:1641px">My Favourite Topics In Exploring My Account On Life So Far In An Opportunity To Frame</p>

  <article class="post" style="left:100px">
    <div class="post-photo" role="img" aria-label="Photo of a seminar audience watching a hair demonstration" style="background:linear-gradient(135deg,#3e4a4f,#8d979a 55%,#2f3538)">
      <div class="post-date"><svg width="16" height="16" viewBox="0 0 16 16"><rect x="1" y="3" width="14" height="12" fill="none" stroke="#fff" stroke-width="2"/><path d="M1 7h14" stroke="#fff" stroke-width="2"/></svg>10 Jun, 2017</div>
    </div>
    <div class="post-meta"><span>👤 posted by Jhon</span><span>0 Comments</span></div>
    <h3>THE STANDARD LOREM IPSUM USED</h3>
    <p>Sed ut perspiciatis unde omnis iste natus error sit voluptatem accusantium doloremque</p>
  </article>

  <article class="post" style="left:446px">
    <div class="post-photo" role="img" aria-label="Photo of a row of hair treatment bottles" style="background:linear-gradient(135deg,#c9cbc4,#e8e9e2 50%,#9fa39a)">
      <div class="post-date"><svg width="16" height="16" viewBox="0 0 16 16"><rect x="1" y="3" width="14" height="12" fill="none" stroke="#fff" stroke-width="2"/><path d="M1 7h14" stroke="#fff" stroke-width="2"/></svg>10 Apr, 2017</div>
    </div>
    <div class="post-meta"><span>👤 posted by Jhon</span><span>0 Comments</span></div>
    <h3>THE STANDARD LOREM IPSUM USED</h3>
    <p>Sed ut perspiciatis unde omnis iste natus error sit voluptatem accusantium doloremque</p>
  </article>

  <article class="post" style="left:795px">
    <div class="post-photo" role="img" aria-label="Photo comparing scalp hair before and after treatment" style="background:linear-gradient(135deg,#5a4536,#b29a86 50%,#4a3a30)">
      <div class="post-date"><svg width="16" height="16" viewBox="0 0 16 16"><rect x="1" y="3" width="14" height="12" fill="none" stroke="#fff" stroke-width="2"/><path d="M1 7h14" stroke="#fff" stroke-width="2"/></svg>10 Mar, 2017</div>
    </div>
    <div class="post-meta"><span>👤 posted by Jhon</span><span>0 Comments</span></div>
    <h3>THE STANDARD LOREM IPSUM USED</h3>
    <p>Sed ut perspiciatis unde omnis iste natus error sit voluptatem accusantium doloremque</p>
  </article>
</section>

<section class="testimonial" role="img" aria-label="Photo of hands combing through a client's hair">
  <span class="quote-rule" style="left:322px"></span>
  <span class="quote-rule" style="left:687px"></span>
  <div class="quote-badge"><svg width="80" height="80" viewBox="0 0 80 80"><text x="40" y="58" text-anchor="middle" font-family="Lato, sans-serif" font-weight="900" font-size="54" fill="#fff">“</text></svg></div>
  <p class="quote-text">“ Lorem Ipsum is simply dummy text of the printing and typesetting<br>industry Lorem Ipsum has been the industry’s ”</p>
  <p class="quote-name">CREATIVE MANAGER</p>
  <div class="dots" style="left:563px;top:316px"><span class="dot"></span><span class="dot on"></span><span class="dot"></span></div>
</section>

<section>
  <h2 class="section-title" style="top:2650px;font-family:'Lato',sans-serif">OUR PARTNERS</h2>
  <p class="section-sub" style="top:2696px">We would like to congratulate the following salons for joining our network and completing “The Science of Hair Loss” seminar</p>
  <div class="partner" style="left:100px"><span></span></div>
  <div class="partner" style="left:304px"><span></span></div>
  <div class="partner" style="left:507px"><span></span></div>
  <div class="partner" style="left:710px"><span></span></div>
  <div class="partner" style="left:914px"><span></span></div>
</section>

<section class="contact">
  <div class="contact-item" style="left:94px">
    <div class="contact-icon"><svg width="28" height="28" viewBox="0 0 28 28"><path d="M6 3c2-1 3 0 4 2l1.5 3c.5 1.5-.5 2.5-2 3.3 1.5 3.2 4 5.7 7.2 7.2.8-1.5 1.8-2.5 3.3-2l3 1.5c2 1 3 2 2 4-2 3-5 3.5-9 1.5-5-2.5-9-6.5-11.5-11.5-2-4-1.5-7 1.5-9z" fill="#fff"/></svg></div>
    (555) 014-2290
  </div>
  <div class="contact-item" style="left:423px">
    <div class="contact-icon"><svg width="24" height="30" viewBox="0 0 24 30"><path d="M12 1a10 10 0 0 0-10 10c0 7 10 18 10 18s10-11 10-18A10 10 0 0 0 12 1z" fill="#fff"/><circle cx="12" cy="11" r="4" fill="#0a5f4c"/></svg></div>
    1820 Linden Ave, Suite 400<br>Harbor City CA 90000
  </div>
  <div class="contact-item" style="left:788px">
    <div class="contact-icon"><svg width="30" height="22" viewBox="0 0 30 22"><rect x="1" y="1" width="28" height="20" rx="2" fill="#fff"/><path d="M2 2l13 10L28 2" fill="none" stroke="#0a5f4c" stroke-width="2"/></svg></div>
    hello@haltandfullmane.example
  </div>
</section>

<footer class="site-footer">
  <p class="copyright">© Copyright 2017 &nbsp;Haltandfullmane. All Rights Reserved</p>
  <div class="social"><span></span><span></span><span></span><span></span><span></span><span></span></div>
</footer>

</body>
</html>
```